Investment company needing business card

We are wanting a business card which looks sharp and easy on the eye. We are thinking of having a business card with the logo embossed on it, to really make it stand out. We will only have a small amount of information of the business card, person's name, position, email address and phone number

Contact Information for Business Card

Danielle Frost
Executive Assistant
+64 21 473 5162
danielf@harwickpartners.co.nz

Requirements
Must have
• Embossed logo
Should not have
• Not to be busy

```html
<!DOCTYPE html>
<html lang="en">
<head>
<meta charset="utf-8">
<title>Harwick Partners – Business Card</title>
<link rel="stylesheet" href="https://fonts.googleapis.com/css2?family=Michroma&family=Open+Sans:wght@400;600&display=swap">
<style>
  :root {
    --backdrop: #e6e4e1;
    --card-top: #2a2a2a;
    --card-bottom: #161616;
    --brand-green: #1fbf7a;
    --text-light: #e9e9e9;
    --text-grey: #a9a9a9;
    --rule-grey: #8a8a8a;
  }
  * { margin: 0; padding: 0; box-sizing: border-box; }
  html, body {
    width: 1200px;
    height: 960px;
    overflow: hidden;
    background: var(--backdrop);
  }
  .canvas {
    position: relative;
    width: 1200px;
    height: 960px;
    display: flex;
    flex-direction: column;
    align-items: center;
    justify-content: center;
    gap: 80px;
  }
  .card {
    position: relative;
    width: 560px;
    height: 320px;
    border-radius: 4px;
    background: linear-gradient(160deg, var(--card-top), var(--card-bottom));
    box-shadow: 0 10px 30px rgba(0,0,0,0.25);
    overflow: hidden;
  }
  .brand {
    display: flex;
    align-items: center;
    gap: 14px;
  }
  .brand-square {
    width: 34px;
    height: 34px;
    background: var(--brand-green);
  }
  .brand-name {
    font-family: "Michroma", sans-serif;
    font-size: 22px;
    font-weight: 400;
    letter-spacing: 1px;
    color: var(--brand-green);
    white-space: nowrap;
  }
  .brand-rule {
    height: 1px;
    background: var(--rule-grey);
    margin-top: 10px;
  }

  /* Front */
  .card-front .front-inner {
    position: absolute;
    inset: 0;
    display: flex;
    flex-direction: column;
    align-items: center;
    justify-content: center;
  }
  .card-front .brand-block { width: 370px; }
  .website-line {
    font-family: "Open Sans", sans-serif;
    font-size: 15px;
    letter-spacing: 2px;
    color: var(--text-light);
    margin-top: 34px;
  }

  /* Back */
  .card-back .brand-block {
    position: absolute;
    left: 34px;
    top: 46px;
    width: 370px;
  }
  .contact-list {
    position: absolute;
    left: 34px;
    bottom: 34px;
    list-style: none;
    font-family: "Open Sans", sans-serif;
    font-size: 13px;
    color: var(--text-light);
  }
  .contact-list li {
    display: flex;
    align-items: center;
    gap: 10px;
    margin-top: 6px;
  }
  .contact-icon { width: 12px; height: 12px; flex: none; }
  .person {
    position: absolute;
    right: 30px;
    bottom: 86px;
    text-align: right;
    font-family: "Michroma", sans-serif;
  }
  .person-name {
    font-size: 15px;
    color: var(--brand-green);
    letter-spacing: 0.5px;
  }
  .person-role {
    font-size: 11px;
    color: var(--text-grey);
    margin-top: 6px;
    letter-spacing: 0.5px;
  }
</style>
</head>
<body>
<main class="canvas">
  <section class="card card-front" aria-label="Card front">
    <div class="front-inner">
      <div class="brand-block">
        <div class="brand">
          <span class="brand-square"></span>
          <span class="brand-name">HARWICK PARTNERS</span>
        </div>
        <div class="brand-rule"></div>
      </div>
      <p class="website-line">www.harwickpartners.com/</p>
    </div>
  </section>

  <section class="card card-back" aria-label="Card back">
    <div class="brand-block">
      <div class="brand">
        <span class="brand-square"></span>
        <span class="brand-name">HARWICK PARTNERS</span>
      </div>
      <div class="brand-rule"></div>
    </div>

    <div class="person">
      <p class="person-name">DANIELLE FROST</p>
      <p class="person-role">EXECUTIVE ASSISTANT</p>
    </div>

    <ul class="contact-list">
      <li>
        <svg class="contact-icon" viewBox="0 0 12 12" aria-hidden="true">
          <circle cx="6" cy="6" r="5.5" fill="none" stroke="#1fbf7a" stroke-width="1"/>
          <path d="M4 3.2 L5 3 L5.6 4.6 L5 5.2 Q5.6 6.6 6.8 7 L7.4 6.4 L9 7 L8.8 8 Q6.5 8.6 4.6 6.6 Q3.4 5 4 3.2 Z" fill="#1fbf7a"/>
        </svg>
        <span>+64 21 473 5162</span>
      </li>
      <li>
        <svg class="contact-icon" viewBox="0 0 12 12" aria-hidden="true">
          <rect x="1" y="3" width="10" height="7" fill="none" stroke="#1fbf7a" stroke-width="1.2"/>
          <path d="M1 3 L6 7 L11 3" fill="none" stroke="#1fbf7a" stroke-width="1.2"/>
        </svg>
        <span>danielf@harwickpartners.co.nz</span>
      </li>
      <li>
        <svg class="contact-icon" viewBox="0 0 12 12" aria-hidden="true">
          <circle cx="6" cy="6" r="5" fill="none" stroke="#1fbf7a" stroke-width="1"/>
          <ellipse cx="6" cy="6" rx="2.2" ry="5" fill="none" stroke="#1fbf7a" stroke-width="0.9"/>
          <line x1="1" y1="6" x2="11" y2="6" stroke="#1fbf7a" stroke-width="0.9"/>
        </svg>
        <span>www.harwickpartners.com/</span>
      </li>
    </ul>
  </section>
</main>
</body>
</html>
```